Flyer Rework for Accountants and Lawyers

Information flyer for accountants and lawyers. Text and flowchart provided. Just need to make it look presentable for print and email. Needs to add logo (AI file provided) and provide graphics. No more than two pages. Our corporate visual identify guidelines are attached (MUST Use). Completed on both AI file and PPTX file.
Target Market(s)
Accountants, Company Directors and Lawyers
Industry/Entity Type
Finance And Accounting
Requirements
Must have
- Our corporate visual identify guidelines are attached (MUST Use)

```html
<!DOCTYPE html>
<html lang="en">
<head>
<meta charset="utf-8">
<title>Fernway Advisory – Director Penalty Notices Flyer</title>
<link rel="stylesheet" href="https://fonts.googleapis.com/css2?family=Montserrat:wght@600;700;800;900&family=Open+Sans:wght@400;600;700&display=swap">
<style>
  :root{
    --green:#4caf2a;
    --green-dark:#3d9321;
    --ink:#1d1d1d;
    --charcoal:#2b2b2b;
    --black:#141414;
    --grey:#6b6b6b;
    --paper:#ffffff;
    --backdrop:#e4e4e4;
    --photo-a:#c9ccd1;
    --photo-b:#f3f3f3;
  }
  *{margin:0;padding:0;box-sizing:border-box}
  html,body{width:1200px;height:900px;overflow:hidden;background:var(--backdrop)}
  body{font-family:"Open Sans",Arial,sans-serif;color:var(--ink);position:relative}
  .page{position:absolute;left:300px;width:600px;height:424px;background:var(--paper);overflow:hidden;box-shadow:0 2px 10px rgba(0,0,0,.12)}
  .page--front{top:16px}
  .page--back{top:460px}
  .shapes{position:absolute;left:0;top:0;z-index:0}
  .abs{position:absolute;z-index:2}

  /* front */
  .brand{left:18px;top:20px;display:flex;align-items:center;gap:8px}
  .brand__dot{width:34px;height:34px;border-radius:50%;background:var(--green);flex:none}
  .brand__name{font-family:"Montserrat",Arial,sans-serif;font-weight:800;font-size:15px;color:var(--green);letter-spacing:.3px;line-height:1;white-space:nowrap}
  .brand__tag{font-size:6.5px;color:var(--grey);margin-top:3px;white-space:nowrap}
  .claim{left:28px;top:146px;font-family:"Montserrat",Arial,sans-serif;font-weight:900;line-height:.95;text-transform:uppercase}
  .claim__small{font-size:14px;color:var(--ink)}
  .claim__big{font-size:41px;color:var(--ink);letter-spacing:-.5px}
  .claim__big--light{color:var(--paper)}
  .intro{left:28px;top:258px;width:235px;font-size:8.3px;line-height:1.4;color:var(--paper)}
  .help{right:18px;top:270px;width:180px;text-align:right;font-family:"Montserrat",Arial,sans-serif;font-weight:700;font-size:13px;line-height:1.2;color:var(--green)}
  .help-text{left:390px;top:308px;width:194px;font-size:7.6px;line-height:1.45;color:var(--charcoal)}
  .web-strip{right:0;bottom:0;width:220px;height:22px;background:var(--black);color:var(--paper);font-size:7.5px;letter-spacing:2.5px;display:flex;align-items:center;justify-content:center;font-weight:600}

  /* back */
  .sheet{left:14px;top:12px;width:278px}
  .bar{font-family:"Montserrat",Arial,sans-serif;font-weight:700;font-size:8.5px;color:var(--paper);text-align:center;padding:3px 0}
  .bar--green{background:var(--green)}
  .bar--dark{background:var(--charcoal)}
  .copy{font-size:6.4px;line-height:1.4;margin:4px 0}
  .copy strong{font-weight:700}
  .facts{display:grid;grid-template-columns:76px 1fr;margin-top:4px;border:1px solid var(--charcoal)}
  .facts__head{font-family:"Montserrat",Arial,sans-serif;font-weight:700;font-size:6.8px;padding:3px 4px}
  .facts__head--label{background:var(--charcoal);color:var(--paper)}
  .facts__head--title{background:var(--paper);color:var(--ink);text-align:center}
  .facts__label{background:var(--green);color:var(--paper);font-weight:700;font-size:6.2px;line-height:1.3;padding:5px 4px;border-top:1px solid rgba(255,255,255,.5);display:flex;align-items:center}
  .facts__text{font-size:6.1px;line-height:1.35;padding:5px 5px 5px 14px;border-top:1px dashed #999;position:relative;display:flex;align-items:center}
  .facts__text::before{content:"";position:absolute;left:3px;top:50%;margin-top:-3px;width:6px;height:6px;border-radius:50%;background:var(--charcoal)}
  .tips{display:grid;grid-template-columns:1fr 1fr;gap:10px;margin-top:5px}
  .tips ul{list-style:none}
  .tips li{font-size:6.1px;line-height:1.35;padding-left:10px;position:relative;margin-bottom:4px}
  .tips li::before{content:"";position:absolute;left:0;top:1px;width:6px;height:6px;border:1px solid var(--charcoal);border-radius:50%}
  .tips p{font-size:6.1px;line-height:1.35}
  .web-foot{text-align:center;font-size:7px;letter-spacing:2.5px;font-weight:600;margin-top:6px}
  .dark-side{left:304px;top:0;width:296px;height:424px;background:var(--black)}
  .split{left:298px;top:0;width:6px;height:424px;background:var(--green)}
  .flow{position:absolute;left:0;top:0}
  .flow text{font-family:"Open Sans",Arial,sans-serif}
</style>
</head>
<body>

<section class="page page--front" aria-label="Flyer front">
  <svg class="shapes" viewBox="0 0 600 424" width="600" height="424">
    <defs>
      <linearGradient id="photoTone" x1="0" y1="0" x2="1" y2="1">
        <stop offset="0" stop-color="#f3f3f3"/>
        <stop offset=".55" stop-color="#c9ccd1"/>
        <stop offset="1" stop-color="#4a5160"/>
      </linearGradient>
    </defs>
    <polygon points="270,0 600,0 600,196 425,245" fill="url(#photoTone)" role="img" aria-label="Photo of two business advisers reviewing documents together"/>
    <polyline points="600,204 428,252" fill="none" stroke="#2b2b2b" stroke-width="4"/>
    <polygon points="0,78 430,240 250,410 0,410" fill="#4caf2a"/>
  </svg>

  <div class="abs brand">
    <span class="brand__dot"></span>
    <div>
      <div class="brand__name">FERNWAY ADVISORY</div>
      <div class="brand__tag">Restructuring &amp; Insolvency Accountants</div>
    </div>
  </div>

  <h1 class="abs claim">
    <span class="claim__small">Independent</span><br>
    <span class="claim__big">Concise</span><br>
    <span class="claim__big claim__big--light">Efficient</span>
  </h1>

  <p class="abs intro">Company directors and their advisers need to be aware that non-lodgement of Business Activity Statements (“BAS”) and Superannuation Guarantee Charge (“SGC”) Statements with the ATO may leave them personally liable for those debts.</p>

  <h2 class="abs help">How Fernway Advisory can help?</h2>
  <p class="abs help-text">Company directors and their advisers need to be aware that non-lodgement of Business Activity Statements (“BAS”) and Superannuation Guarantee Charge (“SGC”) Statements with the ATO may lead to personal liability for those debts.</p>

  <div class="abs web-strip">www.fernwayadvisory.com.au</div>
</section>

<section class="page page--back" aria-label="Flyer back">
  <div class="abs sheet">
    <div class="bar bar--green">Director Penalty Notices (“DPNs”)</div>
    <p class="copy">The ATO uses DPNs and Garnishee Notices to recover outstanding PAYG and SGC debts from directors of companies who fail to pay or report their Tax Debts.</p>
    <p class="copy"><strong>The DPN regime makes directors of companies personally liable. The key facts of DPN regime are outlined below.</strong></p>

    <div class="facts">
      <div class="facts__head facts__head--label">FACTS</div>
      <div class="facts__head facts__head--title">KEY FACTS OF A DIRECTORS PENALTY NOTICE</div>
      <div class="facts__label">Director personal liabilities</div>
      <div class="facts__text">Directors become personally liable for the company's unpaid PAYG and SGC debts once a notice is issued.</div>
      <div class="facts__label">Automatic liability for unreported and unpaid Tax Debts</div>
      <div class="facts__text">Where debts stay unreported after three months, liability attaches automatically and cannot be remitted.</div>
      <div class="facts__label">Avoiding personal liability for directors once they receive a DPN</div>
      <div class="facts__text">Within 21 days the director must pay the debt, appoint an administrator or place the company into liquidation.</div>
      <div class="facts__label">Effect on new directors</div>
      <div class="facts__text">A new director becomes liable 30 days after appointment for debts that remain unpaid.</div>
      <div class="facts__label">Time frames</div>
      <div class="facts__text">The ATO must wait 21 days after giving notice before starting recovery against the director.</div>
    </div>

    <div class="bar bar--dark" style="margin-top:7px">Tips for directors to limit or avoid personal liability</div>
    <div class="tips">
      <ul>
        <li>Always lodge BAS and SGC statements on time, even when the company cannot pay in full.</li>
        <li>Seek early professional advice when cash flow is tight to protect the company and yourself.</li>
      </ul>
      <p>Directors can reduce their exposure by entering a payment arrangement with the ATO before a DPN is issued and by keeping company records current and complete.</p>
    </div>
    <div class="web-foot">www.fernwayadvisory.com.au</div>
  </div>

  <div class="abs dark-side">
    <svg class="flow" viewBox="0 0 296 424" width="296" height="424">
      <g stroke="#4caf2a" stroke-width="2" fill="none">
        <line x1="95" y1="112" x2="95" y2="150"/>
        <line x1="95" y1="150" x2="210" y2="150"/>
        <line x1="210" y1="150" x2="210" y2="112"/>
        <line x1="100" y1="150" x2="100" y2="177"/>
        <line x1="100" y1="253" x2="100" y2="300"/>
        <line x1="60" y1="300" x2="210" y2="300"/>
        <line x1="210" y1="188" x2="210" y2="300"/>
        <line x1="60" y1="300" x2="60" y2="320"/>
        <line x1="210" y1="300" x2="210" y2="320"/>
      </g>
      <g fill="#ffffff" stroke="#4caf2a" stroke-width="4">
        <circle cx="95" cy="70" r="42"/>
        <circle cx="210" cy="150" r="38"/>
        <circle cx="100" cy="215" r="38"/>
      </g>
      <g font-size="6.5" fill="#1d1d1d" text-anchor="middle" font-weight="600">
        <text x="95" y="60">Director receives</text>
        <text x="95" y="69">a Director Penalty</text>
        <text x="95" y="78">Notice from</text>
        <text x="95" y="87">the ATO</text>
        <text x="210" y="142">Were all debts</text>
        <text x="210" y="151">reported within</text>
        <text x="210" y="160">three months?</text>
        <text x="100" y="207">Lockdown DPN</text>
        <text x="100" y="216">issued, liability</text>
        <text x="100" y="225">cannot be remitted</text>
      </g>
      <g font-size="6" font-weight="700" text-anchor="middle">
        <rect x="142" y="143" width="20" height="12" rx="6" fill="#ffffff"/>
        <text x="152" y="151.5" fill="#1d1d1d">No</text>
        <rect x="125" y="294" width="20" height="12" rx="6" fill="#ffffff"/>
        <text x="135" y="302.5" fill="#1d1d1d">Yes</text>
        <rect x="180" y="294" width="20" height="12" rx="6" fill="#ffffff"/>
        <text x="190" y="302.5" fill="#1d1d1d">No</text>
      </g>
      <g font-size="6.3" fill="#ffffff" text-anchor="middle">
        <text x="60" y="332">If directors act within 21 days and</text>
        <text x="60" y="341">appoint an administrator or</text>
        <text x="60" y="350">liquidator, liability is remitted</text>
        <text x="220" y="332">Directors are personally</text>
        <text x="220" y="341">liable for the company's</text>
        <text x="220" y="350">tax debts</text>
      </g>
    </svg>
  </div>
  <div class="abs split"></div>
</section>

</body>
</html>
```